Stonebridge Building and Projects business cards

A business card with watermark background (construction work)

Company logo attached

Home improvement projects
House renovations
Bathroom and kitchen renovations
House extensions
New builds and granny flats

Director Omar Haddani
(Phone number)
omar@sbpbuilding.com.au
(Instagram logo) sbp_building

```html
<!DOCTYPE html>
<html lang="en">
<head>
<meta charset="utf-8">
<title>Stonebridge Building and Projects – Business Cards</title>
<link href="https://fonts.googleapis.com/css2?family=Montserrat:wght@600;700&family=Roboto:wght@400;500;700&display=swap" rel="stylesheet">
<style>
  :root{
    --backdrop:#e4e6e9;
    --card:#fbfbfb;
    --blue:#1874bf;
    --ink:#2f2f31;
    --grey:#6a6c70;
    --faint:#ececee;
  }
  *{box-sizing:border-box;margin:0;padding:0}
  html,body{width:1200px;height:1050px;overflow:hidden}
  body{background:var(--backdrop);font-family:"Roboto",Arial,sans-serif;color:var(--ink);position:relative}
  .card{position:absolute;left:220px;width:760px;height:434px;background:var(--card);border-radius:26px;overflow:hidden;box-shadow:0 8px 22px rgba(0,0,0,.18)}
  .card--front{top:50px}
  .card--back{top:566px}
  .watermark{position:absolute;background:radial-gradient(ellipse at center,var(--faint) 0%,rgba(236,236,238,0) 70%)}
  .brand{position:absolute;text-align:center}
  .brand__name{font-family:"Montserrat",Arial,sans-serif;font-weight:700;color:var(--blue);line-height:1.05}
  .brand__rule{height:2px;background:var(--blue);margin:10px auto}
  .brand__tagline{font-family:"Roboto",Arial,sans-serif;font-weight:500;color:var(--blue);border-bottom:2px solid var(--blue);display:inline-block;padding-bottom:2px}
  /* front */
  .card--front .watermark{left:40px;top:20px;width:680px;height:300px}
  .card--front .brand{left:0;right:0;top:58px}
  .card--front .brand__name{font-size:40px}
  .card--front .brand__rule{width:360px}
  .card--front .brand__tagline{font-size:24px}
  .services{position:absolute;left:0;right:0;top:262px;height:88px;background:var(--blue);color:#fff;font-size:19px;text-align:center;display:flex;flex-direction:column;justify-content:center;gap:6px}
  .services span.sep{padding:0 10px}
  .social-row{position:absolute;left:0;right:0;top:368px;display:flex;justify-content:center;gap:60px;font-size:18px;color:var(--ink)}
  .contact{display:flex;align-items:center;gap:10px}
  .contact svg{width:18px;height:18px;flex:none}
  /* back */
  .side-band{position:absolute;left:0;top:0;bottom:0;width:66px;background:var(--blue)}
  .side-line{position:absolute;left:78px;top:0;bottom:0;width:3px;background:var(--ink)}
  .card--back .watermark{left:470px;top:90px;width:260px;height:190px}
  .card--back .brand{left:120px;top:56px;width:560px}
  .card--back .brand__name{font-size:36px}
  .card--back .brand__rule{width:300px}
  .card--back .brand__tagline{font-size:22px}
  .divider{position:absolute;left:120px;right:40px;top:232px;height:2px;background:var(--blue)}
  .person{position:absolute;left:120px;top:262px}
  .person__name{font-size:30px;font-weight:700;color:var(--blue)}
  .person__title{font-size:19px;color:var(--grey);margin-top:4px}
  .contacts-left{position:absolute;left:120px;top:346px;display:flex;flex-direction:column;gap:12px;font-size:19px}
  .contacts-right{position:absolute;left:420px;top:290px;display:flex;flex-direction:column;gap:12px;font-size:19px}
</style>
</head>
<body>

<section class="card card--front" aria-label="Business card front">
  <div class="watermark" role="img" aria-label="Faint construction work watermark"></div>
  <div class="brand">
    <div class="brand__name">Stonebridge Building<br>and Projects</div>
    <div class="brand__rule"></div>
    <div class="brand__tagline">Solid from the ground up!</div>
  </div>
  <div class="services">
    <div>Home Improvement Projects<span class="sep">|</span>House Renovations<span class="sep">|</span>House Extensions</div>
    <div>Bathroom &amp; Kitchen Renovations<span class="sep">|</span>New Builds &amp; Granny Flats</div>
  </div>
  <div class="social-row">
    <div class="contact">
      <svg viewBox="0 0 20 20"><circle cx="10" cy="10" r="9" fill="var(--blue)"/></svg>
      sbp_building
    </div>
    <div class="contact">
      <svg viewBox="0 0 20 20" fill="none" stroke="var(--blue)" stroke-width="1.6"><circle cx="10" cy="10" r="8.5"/><ellipse cx="10" cy="10" rx="3.8" ry="8.5"/><path d="M1.5 10h17M3 5.5h14M3 14.5h14"/></svg>
      www.sbpbuilding.com.au
    </div>
  </div>
</section>

<section class="card card--back" aria-label="Business card back">
  <div class="side-band"></div>
  <div class="side-line"></div>
  <div class="watermark" role="img" aria-label="Faint construction work watermark"></div>
  <div class="brand">
    <div class="brand__name">Stonebridge Building and Projects</div>
    <div class="brand__rule"></div>
    <div class="brand__tagline">Solid from the ground up!</div>
  </div>
  <div class="divider"></div>
  <div class="person">
    <div class="person__name">Omar Haddani</div>
    <div class="person__title">Managing Director</div>
  </div>
  <div class="contacts-left">
    <div class="contact">
      <svg viewBox="0 0 20 20"><circle cx="10" cy="10" r="9" fill="none" stroke="var(--blue)" stroke-width="1.6"/><path d="M7 5.5l2 2-1.2 1.3c.6 1.3 1.6 2.3 2.9 2.9L12 10.5l2 2-1.3 1.5C9.5 14 6 10.5 5.8 7z" fill="var(--blue)"/></svg>
      0400 318 274
    </div>
    <div class="contact">
      <svg viewBox="0 0 20 20"><circle cx="10" cy="10" r="9" fill="var(--blue)"/></svg>
      sbp_building
    </div>
  </div>
  <div class="contacts-right">
    <div class="contact">
      <svg viewBox="0 0 20 20" fill="none" stroke="var(--blue)" stroke-width="1.6"><rect x="2" y="4.5" width="16" height="11" rx="1.5"/><path d="M2.5 5.5l7.5 6 7.5-6"/></svg>
      omar@sbpbuilding.com.au
    </div>
    <div class="contact">
      <svg viewBox="0 0 20 20" fill="none" stroke="var(--blue)" stroke-width="1.6"><circle cx="10" cy="10" r="8.5"/><ellipse cx="10" cy="10" rx="3.8" ry="8.5"/><path d="M1.5 10h17M3 5.5h14M3 14.5h14"/></svg>
      www.sbpbuilding.com.au
    </div>
  </div>
</section>

</body>
</html>
```